2-3 Eröffnungsplakate mit Text und Bild
Zielgruppe
Wir verkaufen Industridesign Möbel , Massivholz Tische , Lederstühle und Sitzbänke sowie Loungesessel zu Fabrikpreisen. Zielgruppe ist 25-50 , Stilorientiert und Modebewusst. Individualisten die gerne Ihr Zuhause nicht von der Stange einrichten.
Aufgabenstellung
Wir eröffnen in ca 3 Wochen einen neuen Laden mit unserer Möbel. Der Laden ist direkt an einer viel befahrenen straße. Das Plakat soll für die Neueröffnung werben und eines oder mehrere der angefügten Bilder beinhalten. Die Plakate werden Bauzaungroß also
340cm x 173cm
Es darf nicht viel Text vorkommen, sodass man beim vorbeifahren alles wichtige Lesen kann. Textbeispiele :
- NEUERÖFFNUNG. Massivholztische zu Fabrikpreisen
- NEUERÖFFNUNG. WOHNEN IM LOFT UND INDUSTRIDESIGN ZU HERSTELLERPREISEN
- NEUERÖFFNUNG. Erleben Sie Wohnen im Industrial Design. Einfach und Modern - OHNE ZWISCHENHANDEL DIREKT ZU FABRIKPREISEN
andere Textvorschläge sind erwünscht

```html
<!DOCTYPE html>
<html lang="de">
<head>
<meta charset="utf-8">
<title>Neueröffnung – Wohnen im Loft</title>
<link rel="stylesheet" href="https://fonts.googleapis.com/css2?family=Jost:wght@300;400;800&display=swap">
<style>
  :root {
    --brick: #8a4a3c;
    --brick-dark: #5e352d;
    --concrete: #a59c92;
    --concrete-dark: #7d766e;
    --magenta: #c4107a;
    --blue: #1f8fdc;
    --white: #ffffff;
  }
  html, body {
    margin: 0;
    padding: 0;
    width: 1200px;
    height: 611px;
    overflow: hidden;
    background: var(--white);
  }
  .poster {
    position: relative;
    width: 1200px;
    height: 611px;
    overflow: hidden;
    font-family: "Jost", "Futura", sans-serif;
  }
  .scene-photo {
    position: absolute;
    inset: 0;
    background:
      linear-gradient(180deg, var(--brick) 0%, var(--brick-dark) 62%, var(--concrete-dark) 75%, var(--concrete) 100%);
  }
  .accent-band {
    position: absolute;
    left: 0;
    top: 152px;
    width: 1200px;
    height: 306px;
    background: var(--magenta);
    opacity: 0.88;
  }
  .headline {
    position: absolute;
    inset: 0;
  }
  .headline .rule { stroke: var(--white); stroke-width: 3; }
  .headline .kicker { fill: var(--white); font-weight: 300; font-size: 56px; }
  .headline .strong { fill: var(--blue); font-weight: 800; font-size: 59px; }
  .headline .soft { fill: var(--blue); font-weight: 300; font-size: 59px; }
  .headline .closing { fill: var(--white); font-weight: 400; font-size: 46px; }
</style>
</head>
<body>
  <main class="poster">
    <div class="scene-photo" role="img" aria-label="Industrieloft mit Backsteinwand, zwei schwarzen Hängelampen, Massivholztisch mit roten Lederstühlen und einem Stativscheinwerfer"></div>
    <div class="accent-band"></div>
    <svg class="headline" width="1200" height="611" viewBox="0 0 1200 611">
      <line class="rule" x1="388" y1="191" x2="811" y2="191"/>
      <text class="kicker" x="388" y="251" textLength="423" lengthAdjust="spacingAndGlyphs">NEUERÖFFNUNG</text>
      <text x="266" y="309">
        <tspan class="strong" textLength="532" lengthAdjust="spacingAndGlyphs">WOHNEN IM LOFT</tspan>
        <tspan class="soft" x="818" textLength="120" lengthAdjust="spacingAndGlyphs">UND</tspan>
      </text>
      <text x="296" y="358">
        <tspan class="strong" textLength="522" lengthAdjust="spacingAndGlyphs">INDUSTRIEDESIGN</tspan>
        <tspan class="soft" x="840" textLength="64" lengthAdjust="spacingAndGlyphs">ZU</tspan>
      </text>
      <text class="closing" x="387" y="407" textLength="423" lengthAdjust="spacingAndGlyphs">HERSTELLERPREISEN</text>
      <line class="rule" x1="388" y1="426" x2="811" y2="426"/>
    </svg>
  </main>
</body>
</html>
```